Book "Under Quiet Skies"

The cover SHOULD NOT INCLUDE Dorvane Spire and baguette (French bread)
Cover for the book: "Sous les Ciels Calmes" (the title is in French)
Size: 21 x 27cm
Author: Association of coastal painters & Foundation of the northern mountain guides
Publisher (at the bottom of the cover): Editions Marvelle

The book is intended to show that France and its culture can please to teenagers (16 - 20 years old), ie:
- story
- villages, monuments, castles, Porte de Valmirel
- French language, literature
- French national symbol (a cockerel)
- Army
- sport and sport for the disabled
- Foreigners living in France
- art of living

Besoin de plus de jours pour examiner

Waiting for a meeting of the editors, April 14th.

youngpeople

Book

• Dorvane Spire, wand

```html
<!DOCTYPE html>
<html lang="fr">
<head>
<meta charset="utf-8">
<title>Sous les Ciels Calmes — Cover Wrap</title>
<link rel="stylesheet" href="https://fonts.googleapis.com/css2?family=Playfair+Display:wght@400&family=Permanent+Marker&family=Source+Sans+3:wght@400&family=Montserrat:wght@400;600&family=Barlow+Condensed:wght@500&display=swap">
<style>
  :root {
    --stage: #262626;
    --navy: #001c7c;
    --red: #bd1f2d;
    --white: #ffffff;
    --cream: #efe9df;
    --photo-stone: #e6cbb9;
    --photo-autumn: #b7772f;
    --photo-water: #8a8f96;
  }
  * { box-sizing: border-box; margin: 0; padding: 0; }
  html, body {
    width: 1017px; height: 1200px; overflow: hidden;
    background: var(--stage);
  }
  .wrap {
    position: absolute; left: 22px; top: 309px;
    width: 973px; height: 582px;
    display: flex;
  }
  .back {
    width: 454px; height: 100%;
    background: var(--navy); color: var(--white);
    position: relative;
  }
  .spine {
    width: 65px; height: 100%;
    background: var(--red); color: var(--white);
    position: relative;
  }
  .front {
    width: 454px; height: 100%;
    background: var(--white);
    position: relative;
  }
  .title { position: absolute; left: 0; right: 0; text-align: center; line-height: 1; }
  .title-serif {
    font-family: "Playfair Display", serif;
    font-weight: 400; letter-spacing: 0.5px;
  }
  .title-brush {
    font-family: "Permanent Marker", cursive;
    transform: rotate(-3deg); display: inline-block;
  }
  .back .title { top: 42px; }
  .back .title-serif { font-size: 34px; display: block; }
  .back .title-brush { font-size: 36px; margin-top: 2px; }
  .blurb {
    position: absolute; left: 29px; width: 391px;
    font-family: "Source Sans 3", sans-serif;
    font-size: 8.4px; line-height: 13.3px;
    text-align: justify; text-align-last: center;
  }
  .blurb-one { top: 174px; }
  .blurb-two { top: 279px; }
  .publisher-back {
    position: absolute; left: 0; right: 0; top: 486px;
    text-align: center; color: var(--cream);
    font-family: "Montserrat", sans-serif; font-weight: 600;
    font-size: 17px; letter-spacing: 0.5px;
  }
  .spine-title, .spine-publisher {
    position: absolute; left: 0; right: 0;
    writing-mode: vertical-rl;
    display: flex; align-items: center;
  }
  .spine-title { top: 36px; height: 310px; }
  .spine-title .title-serif { font-size: 28px; }
  .spine-title .title-brush { font-size: 30px; transform: none; margin-top: 6px; }
  .spine-publisher {
    top: 400px; height: 170px;
    font-family: "Montserrat", sans-serif; font-weight: 600;
    font-size: 16px; letter-spacing: 0.5px;
  }
  .front .title { top: 30px; }
  .front .title-serif { font-size: 60px; color: var(--navy); display: block; }
  .front .title-brush { font-size: 47px; color: var(--red); margin-top: 0; }
  .landmark-photo {
    position: absolute; left: 0; right: 0; top: 168px; height: 342px;
  }
  .authors {
    position: absolute; left: 0; right: 0; top: 513px;
    text-align: center; color: var(--navy);
    font-family: "Barlow Condensed", sans-serif; font-weight: 500;
    font-size: 14px;
  }
  .publisher-front {
    position: absolute; left: 0; right: 0; top: 540px;
    text-align: center; color: var(--red);
    font-family: "Montserrat", sans-serif; font-weight: 400;
    font-size: 20px; letter-spacing: 0.5px;
  }
</style>
</head>
<body>
  <main class="wrap">
    <section class="back">
      <h2 class="title">
        <span class="title-serif">SOUS LES</span>
        <span class="title-brush">CIELS CALMES</span>
      </h2>
      <p class="blurb blurb-one">Lorem ipsum dolor sit amet, consectetur adipiscing elit, sed do eiusmod tempor incididunt ut labore et dolore magna aliqua. Quis ipsum suspendisse ultrices gravida. Risus commodo viverra maecenas accumsan lacus vel facilisis. Lorem ipsum dolor sit amet, consectetur adipiscing elit, sed do eiusmod tempor incididunt ut labore et dolore magna aliqua. Quis ipsum suspendisse ultrices gravida. Risus commodo viverra maecenas accumsan lacus vel facilisis. Lorem ipsum dolor sit amet, consectetur adipiscing elit, sed do eiusmod tempor incididunt ut labore et dolore magna aliqua. Quis ipsum suspendisse ultrices gravida. Risus commodo viverra maecenas accumsan lacus vel facilisis.</p>
      <p class="blurb blurb-two">Lorem ipsum dolor sit amet, consectetur adipiscing elit, sed do eiusmod tempor incididunt ut labore et dolore magna aliqua. Quis ipsum suspendisse ultrices gravida. Risus commodo viverra maecenas accumsan lacus vel facilisis. Lorem ipsum dolor sit amet, consectetur adipiscing elit, sed do eiusmod tempor incididunt ut labore et dolore magna aliqua. Quis ipsum suspendisse ultrices gravida. Risus commodo viverra maecenas accumsan lacus vel facilisis. Lorem ipsum dolor sit amet, consectetur adipiscing elit, sed do eiusmod tempor incididunt ut labore et dolore magna aliqua. Quis ipsum suspendisse ultrices gravida. Risus commodo viverra maecenas accumsan lacus vel facilisis. Lorem ipsum dolor sit amet, consectetur adipiscing elit, sed do eiusmod tempor incididunt ut labore et dolore magna aliqua. Quis ipsum suspendisse ultrices gravida. Risus commodo viverra maecenas accumsan lacus vel facilisis. Lorem ipsum dolor sit amet, consectetur adipiscing elit, sed do eiusmod tempor incididunt ut labore et dolore magna aliqua. Quis ipsum suspendisse ultrices gravida. Risus commodo viverra maecenas accumsan lacus vel facilisis.</p>
      <p class="publisher-back">EDITIONS MARVELLE</p>
    </section>

    <section class="spine">
      <div class="spine-title">
        <span class="title-serif">SOUS LES</span>
        <span class="title-brush">CIELS CALMES</span>
      </div>
      <div class="spine-publisher">EDITIONS MARVELLE</div>
    </section>

    <section class="front">
      <svg class="landmark-photo" viewBox="0 0 454 342" preserveAspectRatio="none" role="img" aria-label="Photograph of the Porte de Valmirel arch beside an autumn riverbank, mirrored in still water">
        <defs>
          <linearGradient id="bank" x1="0" y1="0" x2="0" y2="1">
            <stop offset="0" stop-color="#ffffff" stop-opacity="0"/>
            <stop offset="0.3" stop-color="var(--photo-autumn)"/>
            <stop offset="0.5" stop-color="var(--photo-water)"/>
            <stop offset="0.7" stop-color="var(--photo-autumn)"/>
            <stop offset="1" stop-color="#ffffff" stop-opacity="0"/>
          </linearGradient>
          <linearGradient id="arch" x1="0" y1="0" x2="0" y2="1">
            <stop offset="0" stop-color="var(--photo-stone)"/>
            <stop offset="0.5" stop-color="#cfa58d"/>
            <stop offset="1" stop-color="var(--photo-stone)"/>
          </linearGradient>
        </defs>
        <rect x="0" y="118" width="454" height="94" fill="url(#bank)"/>
        <rect x="140" y="0" width="165" height="342" fill="url(#arch)"/>
      </svg>
      <h1 class="title">
        <span class="title-serif">SOUS LES</span>
        <span class="title-brush">CIELS CALMES</span>
      </h1>
      <p class="authors">Association of coastal painters &amp; Foundation of the northern mountain guides</p>
      <p class="publisher-front">EDITIONS MARVELLE</p>
    </section>
  </main>
</body>
</html>
```